Diverse, up-scale salon needs eye-catching, unique business cards.

We are looking for a unique business card design for our stylist but that can also be multi functional and used for appointment reminder and referrals. I will need a design in a format that I can modify names and titles going forward. In the past we have had a dark background with the logo on one side, and stylist and contact information on the other but we are open to all ideas. I have included our mission statement as well as branded colors below. The statement doesn't need to go on the card, it's just a reference for target market. We need space for the stylists name, title, instagram handle and then the salons phone number, website and address. I am also open to adding a spot for a qr code linked to the stylist instagram or the salon booking link.

primary brand colors:
#333333 #233415 #36502a #93874a #000000
Mission statement:
Vessolin Hair Studio, a high-end salon located in the lively Downtown Farmington, Michigan, is committed to providing exceptional services in a welcoming and relaxed environment to meet the needs of our diverse clientele.
Our salon specializes in contemporary custom haircuts, coloring, extensions, and barbering and beard grooming services. Our team of skilled stylists is passionate and inventive in their hair styling techniques. At the heart of our salon are values centered on quality, innovation, creativity, and above all, comfort. These core values are evident in every appointment across our customizable array of services.
Our goal is to establish a benchmark for exceptional hair care for every human.
Website: www.vessolinhairstudio.example
instagram: @vessolinhairstudio
address: 41782 Pelham Crest Rd, Farmington MI
phone: 248-613-4087

Industry/Entity Type

Hair Salon

Contact Information for Business Card

Stylist name, title, phone, instagram, website, address, (optional qr code)

Requirements
Should not have
• Does not need mission statement on the card.

```html
<!DOCTYPE html>
<html lang="en">
<head>
<meta charset="utf-8">
<title>Vessolin Hair Studio – Business Card</title>
<link href="https://fonts.googleapis.com/css2?family=Arimo:wght@400;700&display=swap" rel="stylesheet">
<style>
  :root {
    --backdrop: #1c1c1c;
    --olive: #93874a;
    --white: #ffffff;
    --grey-text: #7a7a7a;
    --divider: #8a8a8a;
  }
  * { box-sizing: border-box; margin: 0; padding: 0; }
  html, body {
    width: 1200px; height: 1059px; overflow: hidden;
    background: var(--backdrop);
    font-family: "Arimo", Arial, sans-serif;
  }
  .stage { position: relative; width: 1200px; height: 1059px; }

  .card { position: absolute; box-shadow: 0 10px 30px rgba(0,0,0,.55); }

  /* Front */
  .card--front { left: 258px; top: 89px; width: 689px; height: 394px; background: var(--white); }
  .edge-bar { position: absolute; top: 103px; width: 19px; height: 189px; background: var(--olive); }
  .edge-bar--left { left: 0; }
  .edge-bar--right { right: 0; }

  .brand-mark {
    position: absolute; display: flex; align-items: center; justify-content: center;
    border-radius: 50%; text-align: center;
  }
  .brand-mark--front {
    left: 102px; top: 100px; width: 184px; height: 184px;
    border: 3px solid var(--olive); color: var(--olive);
  }
  .brand-mark__name { font-weight: 700; font-size: 22px; line-height: 1.2; letter-spacing: .5px; }

  .divider { position: absolute; left: 324px; top: 101px; width: 2px; height: 193px; background: var(--divider); }

  .contact { position: absolute; left: 354px; top: 98px; color: var(--grey-text); }
  .contact__name { font-size: 20px; font-weight: 700; color: var(--olive); line-height: 1; }
  .contact__title { font-size: 15px; margin-top: 3px; }
  .contact__address { font-size: 18px; line-height: 24px; margin-top: 20px; }
  .contact__list { list-style: none; margin-top: 10px; }
  .contact__item { display: flex; align-items: center; font-size: 18.5px; height: 28px; }
  .contact__icon { width: 16px; height: 16px; margin-right: 10px; flex: none; color: var(--olive); }

  /* Back */
  .card--back { left: 252px; top: 540px; width: 701px; height: 401px; background: var(--olive); color: var(--white); }
  .services { position: absolute; left: 43px; top: 52px; }
  .services__heading { font-size: 21px; font-weight: 700; letter-spacing: .2px; margin-bottom: 8px; }
  .services__list { list-style: none; }
  .services__item { font-size: 20.5px; line-height: 26.8px; display: flex; align-items: center; }
  .services__item::before {
    content: ""; width: 8px; height: 8px; border-radius: 50%;
    background: var(--white); margin: 0 7px 0 4px;
  }
  .brand-mark--back {
    left: 391px; top: 75px; width: 240px; height: 240px;
    border: 4px solid var(--white); color: var(--white);
  }
  .brand-mark--back .brand-mark__name { font-size: 28px; }
</style>
</head>
<body>
<main class="stage">
  <section class="card card--front" aria-label="Business card front">
    <div class="edge-bar edge-bar--left"></div>
    <div class="edge-bar edge-bar--right"></div>

    <div class="brand-mark brand-mark--front">
      <span class="brand-mark__name">Vessolin<br>Hair Studio</span>
    </div>

    <div class="divider"></div>

    <div class="contact">
      <h1 class="contact__name">MARCUS DELLANO</h1>
      <p class="contact__title">Manager</p>
      <p class="contact__address">41782 Pelham Crest Rd<br>Farmington MI</p>
      <ul class="contact__list">
        <li class="contact__item">
          <svg class="contact__icon" viewBox="0 0 16 16" aria-hidden="true">
            <path fill="currentColor" d="M3.5 1.5l2.2 2.6-1.2 1.7c.9 2 2.5 3.6 4.5 4.6l1.7-1.2 2.6 2.2-1.3 2.1C7 13.3 2.6 8.9 1.4 3z"/>
          </svg>248-613-4087
        </li>
        <li class="contact__item">
          <svg class="contact__icon" viewBox="0 0 16 16" aria-hidden="true">
            <rect x="1.5" y="1.5" width="13" height="13" rx="3" fill="none" stroke="currentColor" stroke-width="2"/>
          </svg>@vessolinhairstudio
        </li>
        <li class="contact__item">
          <svg class="contact__icon" viewBox="0 0 16 16" aria-hidden="true" fill="none" stroke="currentColor" stroke-width="1.2">
            <circle cx="8" cy="8" r="6.8"/>
            <ellipse cx="8" cy="8" rx="3" ry="6.8"/>
            <path d="M1.2 8h13.6M2.2 4.6h11.6M2.2 11.4h11.6"/>
          </svg>www.vessolinhairstudio.example
        </li>
      </ul>
    </div>
  </section>

  <section class="card card--back" aria-label="Business card back">
    <div class="services">
      <h2 class="services__heading">OUR SERVICES</h2>
      <ul class="services__list">
        <li class="services__item">Custom Haircuts</li>
        <li class="services__item">Coloring</li>
        <li class="services__item">Extensions</li>
        <li class="services__item">And Barbering</li>
        <li class="services__item">Beard Grooming</li>
      </ul>
    </div>
    <div class="brand-mark brand-mark--back">
      <span class="brand-mark__name">Vessolin<br>Hair Studio</span>
    </div>
  </section>
</main>
</body>
</html>
```